Brochure for a website accessibility report

This brochure is related to a report that www.qelvantrix.org sell. The report shows the results of an automated audit of a websites accessibility. It shows details of issues found with screen shots, examples of code and provides remediation advice.

The brochure will be a pdf 8.5 inches by 11 inches. It can be anywhere from 6 to 10 pages.

The FlintVue™ name itself should be “Bree Serif” font. The fonts, styles, colors and sizes are up to you.

The images used and logo of the Office of Digital Reachworks and K7P logo are upload

We highlighted in blue page extracts from the report we sell. Do not use the blue highlight, it is merely there to show you where the specific examples of the report we sell are vs the other content in the report. The areas in blue which show the content from the actual report should be shown as an extract of the actual page of the report. You have flexibility to change the layout and the way the content look.

The red square callouts over the blue content are callouts that describe the specific page extracts. We used it as a red callout only so that you would be able to see it. You should change the specific location, look and feel of the callout to be appropriate

Target Market(s)

Marketing and Technical people

Industry/Entity Type

Information Technology

Font styles to use
Sans Serif

Colors

Designer to choose colors to be used in the design.

Requirements
Should not have
• wheelchairs, images of blind people

```html
<!DOCTYPE html>
<html lang="en">
<head>
<meta charset="utf-8">
<title>FlintVue™ Brochure – Pages 2–3</title>
<link href="https://fonts.googleapis.com/css2?family=Bree+Serif&family=Raleway:wght@300;400;600;700&display=swap" rel="stylesheet">
<style>
  :root{
    --bg:#dcdcdc;
    --paper:#f6f6f6;
    --paper-alt:#ececec;
    --green:#22a95e;
    --green-light:#46c27f;
    --green-text:#1f9a55;
    --ink:#222;
    --ink-soft:#444;
    --rule:#b9b9b9;
    --link-blue:#1d5fae;
  }
  *{box-sizing:border-box;margin:0;padding:0}
  html,body{width:1200px;height:840px;overflow:hidden;background:var(--bg)}
  body{position:relative;font-family:'Raleway',sans-serif;color:var(--ink)}

  .page{position:absolute;top:75px;width:500px;height:690px;background:var(--paper);box-shadow:0 6px 24px rgba(0,0,0,.18);overflow:hidden}
  .page--left{left:100px}
  .page--right{left:600px;border-left:1px solid #d2d2d2}

  .brand{position:absolute;top:30px;display:flex;align-items:center;gap:6px}
  .brand__mark{width:12px;height:30px;background:var(--green)}
  .brand__name{font-family:'Raleway',sans-serif;font-weight:700;font-size:6.5px;line-height:1.05;text-transform:uppercase;color:var(--ink);width:60px}
  .page--left .brand{left:32px}
  .page--right .brand{right:32px}

  .edition{position:absolute;top:52px;font-family:'Bree Serif',serif;font-size:10px;color:var(--green-text)}
  .page--left .edition{right:40px}
  .page--right .edition{left:52px}
  .header-rule{position:absolute;top:58px;height:1px;background:var(--rule);width:220px}
  .page--left .header-rule{left:120px}
  .page--right .header-rule{right:120px}

  .title{position:absolute;left:32px;top:100px;font-family:'Bree Serif',serif;font-size:21px;font-weight:400}
  .intro{position:absolute;left:32px;top:144px;width:436px;font-size:10px;line-height:1.5;font-weight:400;color:var(--ink-soft)}
  .intro__cap{float:left;font-family:'Raleway',sans-serif;font-weight:300;color:var(--green);font-size:40px;line-height:.85;margin:2px 4px 0 0}

  .device-band{position:absolute;left:0;right:0;top:212px;height:172px;background:var(--paper-alt)}
  .offer{position:absolute;left:32px;top:222px;width:150px;font-size:9.4px;line-height:1.55;color:var(--ink-soft)}
  .offer p+p{margin-top:11px}
  .devices{position:absolute;left:190px;top:216px;width:280px;height:160px;border-radius:4px;background:linear-gradient(135deg,#3a3f4a 0%,#7a8596 45%,#c9cdd4 100%)}

  .facts{position:absolute;left:30px;top:388px;right:0;height:248px;background:linear-gradient(160deg,var(--green-light),var(--green));padding:16px 14px 0 12px;color:#fff;display:grid;grid-template-columns:1fr 1fr;gap:0 14px}
  .facts__title{font-family:'Bree Serif',serif;font-size:14px;margin-bottom:9px}
  .facts ul{list-style:none}
  .facts li{position:relative;padding-left:11px;font-size:8.4px;line-height:1.5;font-weight:400;margin-bottom:6px;text-align:justify}
  .facts li::before{content:"›";position:absolute;left:0;top:-1px;font-size:10px;font-weight:700}
  .facts li.cont::before{content:""}

  .footer{position:absolute;top:660px;left:32px;right:32px;height:14px;font-size:7.5px}
  .footer__num{position:absolute;top:2px;color:var(--green-text)}
  .footer__url{position:absolute;top:0;font-weight:700;font-size:8px}
  .footer__rule{position:absolute;top:7px;height:1px;background:var(--rule)}
  .page--left .footer__num{left:0}
  .page--left .footer__rule{left:22px;width:290px}
  .page--left .footer__url{right:8px}
  .page--right .footer__url{left:0}
  .page--right .footer__rule{left:80px;width:320px}
  .page--right .footer__num{right:0}

  .ada{position:absolute;left:32px;top:102px;width:436px;font-size:8.2px;line-height:1.45;color:var(--ink-soft);text-align:justify}

  .standard{position:absolute;left:32px;top:188px;width:436px;display:flex;align-items:center;gap:26px}
  .standard__brand{display:flex;align-items:center;gap:8px;width:190px}
  .standard__mark{width:22px;height:22px;background:var(--link-blue)}
  .standard__name{font-family:'Raleway',sans-serif;font-weight:700;font-size:28px;color:var(--link-blue)}
  .standard__text{font-size:9.6px;font-weight:700;line-height:1.45;color:var(--ink)}
  .standard__text span{color:var(--link-blue);font-weight:600}

  .principles{position:absolute;left:32px;top:244px;width:436px;height:224px;background:var(--green);padding:13px 10px 0 10px;display:grid;grid-template-columns:1fr 1fr;gap:0 16px;color:#fff}
  .principle{position:relative;padding-left:12px;margin-bottom:11px;font-size:8.6px;line-height:1.5;text-align:justify}
  .principle::before{content:"›";position:absolute;left:0;top:-1px;font-weight:700}
  .principle h3{font-family:'Bree Serif',serif;font-weight:400;font-size:9.6px}
  .principle .note{color:#d7f2e2}

  .journey{position:absolute;left:32px;top:490px;width:436px;font-size:8.2px;line-height:1.45;color:var(--ink-soft);text-align:justify}
  .report{position:absolute;left:32px;top:550px;width:436px}
  .report__head{font-size:8.2px;font-weight:700;line-height:1.3}
  .report__head b{font-family:'Bree Serif',serif;font-weight:400;font-size:18px;margin-right:4px}
  .report ul{list-style:none;margin-top:8px}
  .report li{position:relative;padding-left:12px;font-size:8px;line-height:1.4;color:var(--ink-soft);margin-bottom:3px}
  .report li::before{content:"";position:absolute;left:0;top:3px;width:6px;height:6px;border-radius:50%;background:var(--link-blue)}
</style>
</head>
<body>

<section class="page page--left">
  <div class="brand"><span class="brand__mark"></span><span class="brand__name">Office of Digital Reachworks</span></div>
  <span class="header-rule"></span>
  <span class="edition">2019 Brochure</span>

  <h1 class="title">FlintVue™</h1>
  <p class="intro"><span class="intro__cap">T</span>he Office of Digital Reachworks (ODR) has been helping eliminate the digital accessibility divide since 2001. We have analyzed more than 51,000 websites and our reports, tools, and services help our clients ensure that their sites are accessible to everyone, regardless of any particular disability or impairment.</p>

  <div class="device-band"></div>
  <div class="offer">
    <p>Now, we're offering our exclusive FlintVue™ report, custom-tailored to your website, to help your organization identify and rectify digital accessibility risks.</p>
    <p>FlintVue™ is the most cost-effective first step on your path to compliance.</p>
  </div>
  <div class="devices" role="img" aria-label="Website shown on a desktop monitor, laptop, tablet and phone"></div>

  <div class="facts">
    <div>
      <h2 class="facts__title">QUICK FACTS:</h2>
      <ul>
        <li>Failure to comply with Web Content Accessibility Guidelines (WCAG) 2.1 Level A/AA could result in tens of thousands of dollars (per incident) in legal fees from pending lawsuits.</li>
        <li>Last year the number of website accessibility lawsuits increased by 177% vs. 2017.</li>
        <li>In New York state alone, 1,564 lawsuits were filed alleging websites were not accessible to the blind or visually impaired.</li>
        <li>The cost of making websites accessible ranges from several thousand dollars to</li>
      </ul>
    </div>
    <ul>
      <li class="cont">a few million dollars, depending on the complexity of the site.</li>
      <li>And while numerous big-name companies have been sued (Newsline 9, Grillmonarch, Parcelora, Cocobridge, Pixelvane, Tunewell, Tri-Harbor, Linen Loft &amp; More, Marlow Index, Valumart, Dishdash, Green Ladle, Carewise, Slicepoint, Streamly, Stridon, Kindred Match, Bank of Northfield, Harvest Lane, Keystone Hardware, and hundreds more), small businesses also face great risk.</li>
      <li>Trying to meet WCAG guidelines without the advantage of FlintVue™ could result in a tremendous amount of wasted time, money and effort. Don't go it alone.</li>
    </ul>
  </div>

  <div class="footer"><span class="footer__num">2</span><span class="footer__rule"></span><span class="footer__url">www.qelvantrix.org</span></div>
</section>

<section class="page page--right">
  <span class="edition">2019 Brochure</span>
  <span class="header-rule"></span>
  <div class="brand"><span class="brand__mark"></span><span class="brand__name">Office of Digital Reachworks</span></div>

  <p class="ada">The Americans with Disabilities Act (ADA) is a comprehensive federal civil rights law prohibiting discrimination on the basis of disability, enforced by the Department of Justice (DOJ). The ADA prohibits discriminatory lack of access for individuals with disabilities to goods and services of public services and accommodations. Websites are considered places of public accommodations. The DOJ currently uses WCAG 2.1 Level A/AA as an accepted standard by which to measure a website's accessibility.</p>

  <div class="standard">
    <div class="standard__brand"><span class="standard__mark"></span><span class="standard__name">K7P</span></div>
    <p class="standard__text"><span>WCAG 2.1 Level A/AA</span> consists of 13 guidelines with 50 checkpoints that are organized under four principles:</p>
  </div>

  <div class="principles">
    <div>
      <div class="principle"><h3>Principle 1: Perceivable</h3><span>Information and user interface components must be presented to users in ways they can perceive. This means that users must be able to comprehend the information being depicted:</span> <span class="note">It can't be invisible to all their senses.</span></div>
      <div class="principle"><h3>Principle 2: Operable</h3><span>User interface components and navigation must be operable:</span> <span class="note">The interface cannot require interaction that a user cannot perform.</span></div>
    </div>
    <div>
      <div class="principle"><h3>Principle 3: Understandable</h3><span>Information and the operation of a user interface must be understandable:</span> <span class="note">Users must be able to understand the information as well as the operation of the user interface.</span></div>
      <div class="principle"><h3>Principle 4: Robust</h3><span>Content must be robust enough that it can be interpreted reliably by a wide variety of user agents, including assistive technologies:</span> <span class="note">As technologies and user agents evolve, the content should remain accessible.</span></div>
    </div>
  </div>

  <p class="journey">Start your journey to a fully compliant website with FlintVue™. This detailed compliance and remediation report is generated based on scanning your website against hundreds of carefully-crafted rules, logging failures, and then generating feedback and recommendations on how to fix the problems based on our years of experience and proven best practices.</p>

  <div class="report">
    <p class="report__head"><b>The FlintVue™</b>report is designed to be shared with your executive team and stakeholders. It is divided into two sections to build knowledge and self-sufficiency.</p>
    <ul>
      <li>The first section provides a detailed analysis of your website per the WCAG 2.1 A/AA principles and includes an at-a-glance Summary Chart for your executive team.</li>
      <li>The second section is designed specifically for your website development team, providing them with detailed examples of problematic issues, suggested ways to fix them, and links for more detailed training.</li>
    </ul>
  </div>

  <div class="footer"><span class="footer__url">www.qelvantrix.org</span><span class="footer__rule"></span><span class="footer__num">3</span></div>
</section>

</body>
</html>
```